Fernway goods

Organic ethical yoga/activewear that supports kids in need and other community projects by donating % of all sales to these causes. See the product and the brand (Tamrin project) story and catalogue on
Fernwaygoods.com.au
http://files.brisvault.net/doc/q7k2m9_a41c88e0b3d94f27a615c0e2d9b7f443.pdf
Flyer is for fernway goods as the distributor for Tamrin clothing
Would like the flyer to be simple with core message and contact and site details but have a similar feel to the catalogue using some of the art graphics and or photo from site for colour. Also for wholesale/distributor enquiries or to arrange an appointment for a brand presentation contact Marla Quint 0512
Updates
I have four that I am considering so please don't submit any more. One of these will be suitable. Thanks for your submissions.
Marla
Target Market(s)
Yoga studios, wellness centres , private parties, gyms, agents
Industry/Entity Type
Clothing
Look and feel
Each slider illustrates characteristics of the customer's brand and the style your logo design should communicate.

```html
<!DOCTYPE html>
<html lang="en">
<head>
<meta charset="utf-8">
<title>Fernway goods – Flyer</title>
<link rel="stylesheet" href="https://fonts.googleapis.com/css2?family=Amatic+SC:wght@400;700&display=swap">
<style>
  :root {
    --backdrop: #e3eaee;
    --paper: #ffffff;
    --ink: #1f1d1d;
    --ink-soft: #3a3838;
    --stone: #cfc6b6;
    --stone-light: #e2dccf;
    --aqua: #8fcfd8;
    --aqua-deep: #6fbcc8;
    --berry: #8a3a6a;
    --white: #ffffff;
  }
  * { margin: 0; padding: 0; box-sizing: border-box; }
  html, body {
    width: 1200px;
    height: 1000px;
    overflow: hidden;
    background: var(--backdrop);
    font-family: "Amatic SC", cursive;
  }
  .flyer {
    position: absolute;
    left: 260px;
    top: 20px;
    width: 680px;
    height: 960px;
    background: var(--paper);
    overflow: hidden;
  }
  .flyer__photo {
    position: absolute;
    left: 0; top: 0;
    width: 680px;
    height: 646px;
    background: linear-gradient(180deg,
      var(--stone) 0%,
      var(--stone-light) 18%,
      var(--aqua) 34%,
      var(--aqua-deep) 50%,
      var(--stone-light) 70%,
      var(--aqua) 86%,
      var(--ink-soft) 100%);
  }
  .flyer__brand {
    position: absolute;
    left: 0; top: 300px;
    width: 680px;
    text-align: center;
    color: var(--white);
    font-size: 54px;
    font-weight: 400;
    letter-spacing: 1px;
  }
  .flyer__brand-rule {
    position: absolute;
    left: 190px;
    width: 300px;
    height: 3px;
    background: var(--white);
  }
  .flyer__brand-rule--top { top: 282px; }
  .flyer__brand-rule--bottom { top: 382px; }
  .tagline {
    position: absolute;
    left: 75px; top: 681px;
    width: 527px; height: 103px;
    background: var(--ink);
    color: var(--white);
    text-align: center;
    font-size: 30px;
    line-height: 38px;
    padding-top: 13px;
    letter-spacing: 1px;
  }
  .divider {
    position: absolute;
    left: 253px; top: 812px;
    width: 167px; height: 3px;
    background: var(--ink);
  }
  .contact {
    position: absolute;
    left: 22px; top: 846px;
    width: 640px;
    display: flex;
    align-items: flex-start;
    color: var(--ink);
    font-weight: 700;
  }
  .contact__lead { font-size: 22px; width: 318px; line-height: 28px; }
  .contact__block { font-size: 17px; line-height: 21px; white-space: nowrap; }
  .contact__block--person { width: 135px; }
  .contact__block--web { width: 190px; }
  .pattern-band {
    position: absolute;
    left: 0; top: 912px;
    width: 680px; height: 36px;
    background: linear-gradient(90deg, var(--aqua), var(--berry), var(--aqua), var(--berry), var(--aqua));
    opacity: 0.45;
  }
</style>
</head>
<body>
  <main class="flyer">
    <div class="flyer__photo" role="img" aria-label="Photo of a woman against a sandstone wall holding out an aqua and cream patterned wrap"></div>
    <div class="flyer__brand-rule flyer__brand-rule--top"></div>
    <div class="flyer__brand">Fernway goods</div>
    <div class="flyer__brand-rule flyer__brand-rule--bottom"></div>

    <div class="tagline">Ethical, conscious and organic products<br>supporting the community</div>

    <div class="divider"></div>

    <div class="contact">
      <div class="contact__lead">For wholesale/distributor enquiries contact:</div>
      <div class="contact__block contact__block--person">Head Office - Marla Quint<br>Tel: 0512 374 61</div>
      <div class="contact__block contact__block--web">Fernwaygoods.com.au<br>info@fernwaygoods.com.au</div>
    </div>

    <div class="pattern-band" role="img" aria-label="Decorative band of aqua and berry zigzag lines"></div>
  </main>
</body>
</html>
```